Website for IT consulting Company

I need a website upgrade, the existing site content is ok, I would also like to add a testimonial page, the site should be something that is easy for us to update content. You use the content from www.kelvanbrook.com as an example. I will also post update logo and artwork. I also need a contact form with some type of validation or captcha.

I added Coded to the Project

Please omit Address maps

Target Market(s)

small business, service oriented companies. We provide IT Consulting, support and mangement

Industry/Entity Type

Information Technology

Coding

Number of Pages Required

1 page

Font styles to use
Serif
Sans Serif

Requirements
Must have
• Contain logo attached, and content from existing web site www.kelvanbrook.com.
• Also need to update content easily, and be movable to different platforms.
• There is a catch phrase
• "Let us worry about your technology…” “ so you don’t have to!”
• Should be included.
Nice to have
• Testimonial page, Project page where we can post new and past projects and pictures
Should not have
• none

```html
<!DOCTYPE html>
<html lang="en">
<head>
<meta charset="utf-8">
<title>Kelvanbrook Group, Inc</title>
<link href="https://fonts.googleapis.com/css2?family=Nothing+You+Could+Do&family=Roboto+Condensed:wght@400;700&family=Roboto:wght@400;500&display=swap" rel="stylesheet">
<style>
  :root {
    --brand-blue: #2f8fd8;
    --brand-blue-dark: #1f78c1;
    --ink: #1c1c1c;
    --text: #333;
    --muted: #6d6d6d;
    --bar-bg: #f1f2f4;
    --white: #fff;
    --hero-a: #5b6472;
    --hero-b: #8b95a3;
    --hero-c: #a9b3c0;
  }
  * { box-sizing: border-box; margin: 0; padding: 0; }
  html, body { width: 1200px; height: 676px; overflow: hidden; background: var(--white); }
  body { font-family: "Roboto", Arial, sans-serif; color: var(--text); position: relative; }

  .site-header {
    position: absolute; top: 0; left: 0; width: 1200px; height: 70px;
    background: var(--brand-blue); z-index: 3;
  }
  .brand {
    position: absolute; left: 46px; top: 0; width: 216px; height: 78px;
    background: var(--white); border-radius: 0 0 4px 4px;
    box-shadow: 0 2px 4px rgba(0,0,0,.15);
    display: flex; flex-direction: column; justify-content: center; padding-left: 14px;
  }
  .brand-row { display: flex; align-items: center; gap: 8px; }
  .brand-mark { width: 18px; height: 18px; background: var(--brand-blue); border-radius: 50%; }
  .brand-name { font-family: "Roboto Condensed", Arial, sans-serif; font-weight: 700; font-size: 26px; color: var(--brand-blue-dark); letter-spacing: .5px; }
  .brand-tagline { font-family: "Roboto Condensed", Arial, sans-serif; font-size: 7.5px; color: var(--brand-blue-dark); margin-top: 4px; }

  .main-nav {
    position: absolute; right: 110px; top: 0; height: 70px;
    display: flex; align-items: center; gap: 36px;
    font-family: "Roboto Condensed", Arial, sans-serif; font-size: 14px; color: var(--white);
  }

  .hero {
    position: absolute; top: 70px; left: 0; width: 1200px; height: 450px;
    background: linear-gradient(125deg, var(--hero-b) 0%, var(--hero-c) 35%, var(--hero-a) 70%, #49515e 100%);
    display: flex; flex-direction: column; align-items: center; justify-content: center;
    color: var(--white); text-align: center; padding-top: 20px;
  }
  .hero-title { font-family: "Nothing You Could Do", cursive; font-size: 28px; letter-spacing: 1px; font-weight: 400; }
  .hero-sub { font-family: "Roboto Condensed", Arial, sans-serif; font-size: 15px; margin-top: 14px; }
  .hero-button {
    margin-top: 16px; padding: 6px 18px; border: 1px solid rgba(255,255,255,.8);
    border-radius: 4px; font-family: "Roboto Condensed", Arial, sans-serif; font-size: 12px; color: var(--white);
  }

  .contact-bar {
    position: absolute; top: 520px; left: 0; width: 1200px; height: 30px;
    background: var(--bar-bg); border-bottom: 1px solid #dfe1e4;
    display: flex; align-items: center; padding: 0 100px 0 94px;
    font-family: "Roboto Condensed", Arial, sans-serif; font-size: 13px; color: var(--muted);
  }
  .contact-item { display: flex; align-items: center; gap: 6px; margin-right: 28px; }
  .social { margin-left: auto; display: flex; align-items: center; gap: 14px; }
  .social-square { width: 18px; height: 18px; background: #9aa3ad; border-radius: 3px; }

  .welcome { position: absolute; top: 550px; left: 0; width: 1200px; height: 126px; text-align: center; padding-top: 12px; }
  .welcome-title { font-size: 20px; font-weight: 500; color: var(--ink); }
  .welcome-title span { color: var(--brand-blue-dark); }
  .welcome-rule { width: 1050px; margin: 10px auto 12px; border-top: 1px dashed var(--brand-blue); }
  .welcome-text { width: 1060px; margin: 0 auto; font-size: 12.5px; line-height: 17px; color: var(--text); }
</style>
</head>
<body>
  <header class="site-header">
    <div class="brand">
      <div class="brand-row">
        <span class="brand-mark"></span>
        <span class="brand-name">Kelvanbrook.com</span>
      </div>
      <div class="brand-tagline">Let us worry about your technology… So you don't have to!</div>
    </div>
    <nav class="main-nav">
      <span>HOME</span><span>ABOUT</span><span>SUPPORT</span><span>CLIENTS</span><span>PROJECT</span><span>CAREERS</span><span>CONTACT</span>
    </nav>
  </header>

  <section class="hero" role="img" aria-label="Photo of business people reviewing charts on a tablet beside a coffee cup">
    <h1 class="hero-title">IT solutions that work for your business.</h1>
    <p class="hero-sub">A full service technology company.</p>
    <span class="hero-button">Learn More</span>
  </section>

  <div class="contact-bar">
    <span class="contact-item">
      <svg width="12" height="12" viewBox="0 0 24 24"><path fill="#6d6d6d" d="M6.6 10.8a15 15 0 0 0 6.6 6.6l2.2-2.2c.3-.3.7-.4 1-.2 1.1.4 2.3.6 3.6.6.6 0 1 .4 1 1V20c0 .6-.4 1-1 1A17 17 0 0 1 3 4c0-.6.4-1 1-1h3.5c.6 0 1 .4 1 1 0 1.3.2 2.5.6 3.6.1.3 0 .7-.2 1z"/></svg>
      +1 800 555 01 47
    </span>
    <span class="contact-item">
      <svg width="13" height="10" viewBox="0 0 26 20"><rect x="1" y="1" width="24" height="18" fill="#6d6d6d"/><path d="M1 1l12 10L25 1" fill="none" stroke="#f1f2f4" stroke-width="2"/></svg>
      info@kelvanbrook.com
    </span>
    <div class="social">
      <span class="social-square"></span><span class="social-square"></span><span class="social-square"></span>
      <svg width="13" height="13" viewBox="0 0 24 24"><circle cx="10" cy="10" r="6.5" fill="none" stroke="#6d6d6d" stroke-width="3"/><path d="M15 15l7 7" stroke="#6d6d6d" stroke-width="3"/></svg>
    </div>
  </div>

  <section class="welcome">
    <h2 class="welcome-title">Welcome to <span>Kelvanbrook Group, Inc</span></h2>
    <div class="welcome-rule"></div>
    <p class="welcome-text">Outsourcing is subcontracting a process, such as product design or manufacturing, to a third-party company.[1] The decision to outsource is often made in the interest of lowering firm costs, redirecting or conserving energy directed at the competencies of a particular business, or to make more efficient use of land, labor, capital, (information) technology and resources. Outsourcing became part of the business lexicon during the 1980s</p>
  </section>
</body>
</html>
```